Brisk Harbor claims recovery services

Its a new company in Dubai UAE. The company activity is debt management, debt collection, loans settlements and restructuring. The company involved in any business or sector requires debt management including government entities, Medical & Health care sector, Banks & finance companies, SME's and commercial business.

Target Market(s)

government entities, Medical & Health care sector, Banks & finance companies, SME's and commercial business.

Industry/Entity Type

Financial Service

Number of Pages Required

5+ page

Requirements
Must have
• Focus on the services not the team and clients
Should not have
• Colorful . Shouldn't have Client testimonial and our clients

```html
<!DOCTYPE html>
<html lang="en">
<head>
<meta charset="utf-8">
<title>Brisk Harbor — Claims Recovery Services</title>
<link href="https://fonts.googleapis.com/css2?family=Cinzel:wght@400;600&family=Lato:wght@400;700&display=swap" rel="stylesheet">
<style>
:root{
  --navy:#234a70;
  --navy-dark:#1c3b5a;
  --ink:#1f1f1f;
  --muted:#444;
  --light:#f3f3f3;
  --black:#000;
  --white:#fff;
  --footer:#1a1a1a;
}
*{margin:0;padding:0;box-sizing:border-box}
html,body{width:669px;height:1200px;overflow:hidden;background:var(--white)}
body{position:relative;font-family:"Lato",sans-serif;color:var(--ink)}
.abs{position:absolute}

/* header */
.site-header{position:absolute;left:0;top:0;width:669px;height:53px;background:var(--white)}
.brand{position:absolute;left:54px;top:14px;display:flex;align-items:center;gap:7px}
.brand-dot{width:22px;height:22px;border-radius:50%;background:var(--navy)}
.brand-name{font-family:"Cinzel",serif;font-size:17px;color:var(--navy);letter-spacing:.5px}
.contact{position:absolute;top:19px;display:flex;align-items:center;gap:7px;font-size:9px;color:var(--ink)}
.contact svg{width:16px;height:16px}

/* nav */
.main-nav{position:absolute;left:0;top:53px;width:669px;height:25px;background:linear-gradient(#9a9a9a,#7b7b7b);display:flex;padding-left:55px}
.main-nav a{font-family:"Cinzel",serif;font-size:8.5px;color:var(--white);text-decoration:none;display:flex;align-items:center;justify-content:center;border-right:1px solid #6d6d6d}
.main-nav a.active{background:var(--navy)}

/* hero */
.hero{position:absolute;left:0;top:78px;width:669px;height:287px;background:linear-gradient(90deg,#2a5278 0%,#244a6d 45%,#3b3f46 75%,#2b2d31 100%)}
.hero-floor{position:absolute;left:0;bottom:0;width:669px;height:60px;background:linear-gradient(#cfd3d6,#eef0f1)}
.hero-tag{position:absolute;left:54px;top:91px;width:306px;height:47px;background:rgba(15,15,15,.88);padding:4px 8px;font-family:"Cinzel",serif;color:var(--white);font-size:14.6px;line-height:20px;white-space:nowrap}
.dots{position:absolute;left:311px;top:262px;display:flex;gap:5px}
.dots i{width:8px;height:8px;border-radius:50%;background:#333;border:1px solid #999}
.dots i.on{background:var(--navy)}

/* welcome */
.welcome{position:absolute;left:0;top:365px;width:669px;height:203px;background:var(--light)}
.section-title{position:absolute;left:0;width:669px;text-align:center;font-family:"Cinzel",serif;font-size:16.5px;letter-spacing:.5px}
.section-title .hl{color:var(--navy)}
.divider{position:absolute;left:50%;height:1px}
.divider::after{content:"";position:absolute;left:50%;top:-3px;width:7px;height:7px;margin-left:-3.5px;border-radius:50%;background:var(--navy)}
.intro{position:absolute;left:60px;top:68px;width:549px;font-size:7px;line-height:12.5px;text-align:center;color:var(--ink)}
.pillar{position:absolute;top:119px;width:180px;height:60px}
.pillar-icon{position:absolute;left:0;top:0;width:52px;height:52px;border-radius:50%;background:var(--navy);border:3px solid #d9d9d9;box-shadow:0 1px 3px rgba(0,0,0,.25)}
.pillar-icon svg{position:absolute;left:11px;top:11px;width:24px;height:24px}
.pillar h3{position:absolute;left:65px;top:0;font-family:"Cinzel",serif;font-weight:400;font-size:11.5px}
.pillar p{position:absolute;left:64px;top:18px;width:112px;font-size:7px;line-height:12.5px;color:var(--muted)}
.pillar-sep{position:absolute;top:126px;width:1px;height:50px;background:#d6d6d6}

/* services */
.services{position:absolute;left:0;top:568px;width:669px;height:309px;background:var(--black)}
.services .section-title{color:var(--white);top:22px}
.card{position:absolute;top:69px;width:107px;height:208px;background:var(--white);border-bottom:3px solid var(--navy)}
.card-photo{width:107px;height:92px}
.card-badge{position:absolute;left:44px;top:84px;width:18px;height:18px;border-radius:50%;background:var(--white)}
.card-badge::after{content:"";position:absolute;left:5px;top:5px;width:8px;height:8px;border-radius:50%;background:var(--navy)}
.card h3{position:absolute;left:0;width:107px;top:103px;text-align:center;font-family:"Cinzel",serif;font-weight:400;font-size:10px;line-height:11px}
.card p{position:absolute;left:5px;width:97px;top:134px;text-align:center;font-size:6.6px;line-height:10.5px;color:var(--ink)}
.card-more{position:absolute;left:45px;bottom:-4px;width:17px;height:17px;border-radius:50%;background:var(--navy);color:var(--white);font-size:11px;line-height:16px;text-align:center}

/* covering */
.covering{position:absolute;left:0;top:877px;width:669px;height:269px;background:linear-gradient(#f5f5f5,#ececec);overflow:hidden}
.covering .section-title{top:21px}
.cov-label{position:absolute;font-family:"Cinzel",serif;font-size:8px;color:var(--ink);letter-spacing:.3px}
.hub-name{position:absolute;left:264px;top:226px;width:140px;text-align:center;font-family:"Cinzel",serif;font-size:12px;color:var(--navy)}

/* footer */
.site-footer{position:absolute;left:0;top:1146px;width:669px;height:30px;background:var(--footer);color:#e6e6e6;font-size:8.5px}
.foot-item{position:absolute;top:9px;display:flex;align-items:center;gap:5px}
.foot-item svg{width:11px;height:12px}
.social{position:absolute;left:541px;top:6px;display:flex;gap:4px}
.social i{width:15px;height:15px;border-radius:50%;background:var(--white)}
.copyright{position:absolute;left:0;top:1176px;width:669px;height:24px;background:var(--navy);color:var(--white);font-size:7.5px;text-align:center;line-height:24px}
</style>
</head>
<body>

<header class="site-header">
  <div class="brand"><span class="brand-dot"></span><span class="brand-name">Brisk Harbor</span></div>
  <div class="contact" style="left:404px">
    <svg viewBox="0 0 16 16"><path d="M8 1 L15 8 L8 15 L1 8Z" fill="none" stroke="#234a70" stroke-width="2"/><path d="M6 6c0 2 2 4 4 4" stroke="#234a70" stroke-width="1.4" fill="none"/></svg>
    123-456-7890
  </div>
  <div class="contact" style="left:510px">
    <svg viewBox="0 0 16 16"><path d="M8 1 L15 8 L8 15 L1 8Z" fill="none" stroke="#234a70" stroke-width="2"/><rect x="5" y="6" width="6" height="4" fill="#234a70"/></svg>
    info@briskharbor.com
  </div>
</header>

<nav class="main-nav">
  <a class="active" style="width:53px">Home</a>
  <a style="width:168px">About Us</a>
  <a style="width:170px">Our Services</a>
  <a style="width:168px;border-right:0">Contact Us</a>
</nav>

<section class="hero" role="img" aria-label="Photo of a businessman's hand stopping a row of falling wooden dominoes">
  <div class="hero-floor"></div>
  <div class="hero-tag">Managing your money<br>recovering your relationships</div>
  <div class="dots"><i class="on"></i><i></i><i></i><i></i></div>
</section>

<section class="welcome">
  <h2 class="section-title" style="top:21px">Welcome to <span class="hl">Brisk Harbor.</span></h2>
  <div class="divider" style="top:50px;width:256px;margin-left:-128px;background:var(--navy)"></div>
  <p class="intro">We are a Claims Recovery and Debt Management Services company based in Dubai, United Arab Emirates. The Brisk Harbor team handles a comprehensive range of debt recoveries, such as invoices; insurance payments; supplier and rent payments; and personal and business loans, for individuals and businesses across an array of industries. Brisk Harbor was founded on traditional values, and we're proud of our personal approach.</p>

  <div class="pillar" style="left:60px">
    <div class="pillar-icon"><svg viewBox="0 0 24 24"><circle cx="12" cy="12" r="10" fill="none" stroke="#fff" stroke-width="2"/><circle cx="12" cy="12" r="5.5" fill="none" stroke="#fff" stroke-width="2"/><circle cx="12" cy="12" r="1.8" fill="#fff"/><path d="M12 12 L22 3" stroke="#fff" stroke-width="2"/></svg></div>
    <h3>Mission</h3>
    <p>Brisk Harbor is a leading Debt Management and Claims Recovery Services..... [ + ]</p>
  </div>
  <div class="pillar-sep" style="left:240px"></div>
  <div class="pillar" style="left:256px">
    <div class="pillar-icon"><svg viewBox="0 0 24 24"><path d="M1 12 Q12 2 23 12 Q12 22 1 12Z" fill="none" stroke="#fff" stroke-width="2"/><circle cx="12" cy="12" r="4" fill="#fff"/></svg></div>
    <h3>Vision</h3>
    <p>Our success is built on traditions of trust, valued and respect .....[ +]</p>
  </div>
  <div class="pillar-sep" style="left:436px"></div>
  <div class="pillar" style="left:452px">
    <div class="pillar-icon"><svg viewBox="0 0 24 24"><path d="M1 9 L7 6 L12 9 L17 6 L23 9 M4 11 L10 17 Q12 18 14 16 L20 11" fill="none" stroke="#fff" stroke-width="2" stroke-linejoin="round"/></svg></div>
    <h3>Values</h3>
    <p>At Brisk Harbor, our values are born of time-honoured traditions... [ + ]</p>
  </div>
</section>

<section class="services">
  <h2 class="section-title">Our Services</h2>
  <div class="divider" style="top:50px;width:132px;margin-left:-66px;background:#777"></div>

  <article class="card" style="left:55px">
    <div class="card-photo" role="img" aria-label="Photo of business people reviewing charts on a tablet" style="background:linear-gradient(135deg,#5b6b7c,#c9d3dc)"></div>
    <span class="card-badge"></span>
    <h3>Recovery<br>Solutions</h3>
    <p>Our experience has taught us that when it comes to recovery, it always pays to find the most amicable solution,</p>
    <span class="card-more">+</span>
  </article>
  <article class="card" style="left:168px">
    <div class="card-photo" role="img" aria-label="Photo of a calculator, pen and financial bar charts" style="background:linear-gradient(135deg,#8fa6bb,#e3eaf0)"></div>
    <span class="card-badge"></span>
    <h3>Debt<br>Management</h3>
    <p>At Brisk Harbor, we pull together our wisdom and expertise to make debt work for you.</p>
    <span class="card-more">+</span>
  </article>
  <article class="card" style="left:281px">
    <div class="card-photo" role="img" aria-label="Illustration of a magnifying glass over red debt settlement lettering" style="background:linear-gradient(135deg,#f2f2f2,#d9b4b4)"></div>
    <span class="card-badge"></span>
    <h3>Debt<br>Settlement</h3>
    <p>Lorem ipsum dolor sit amet, consectetuer adipiscing elit, sed diam nonummy nibh euismod tincidunt ut laoreet dolore</p>
    <span class="card-more">+</span>
  </article>
  <article class="card" style="left:394px">
    <div class="card-photo" role="img" aria-label="Photo of business partners shaking hands in an office" style="background:linear-gradient(135deg,#dfe4ea,#7c8896)"></div>
    <span class="card-badge"></span>
    <h3 style="top:108px">Outsourcing</h3>
    <p>Lorem ipsum dolor sit amet, consectetuer adipiscing elit, sed diam nonummy nibh euismod tincidunt ut laoreet dolore</p>
    <span class="card-more">+</span>
  </article>
  <article class="card" style="left:507px">
    <div class="card-photo" role="img" aria-label="Photo of hands typing on a keyboard in blue light" style="background:linear-gradient(135deg,#6f8fae,#2d4a68)"></div>
    <span class="card-badge"></span>
    <h3>Interactive<br>Online Access</h3>
    <p>Lorem ipsum dolor sit amet, consectetuer adipiscing elit, sed diam nonummy nibh euismod tincidunt ut laoreet dolore</p>
    <span class="card-more">+</span>
  </article>
</section>

<section class="covering">
  <h2 class="section-title">We are <span class="hl">Covering</span></h2>
  <div class="divider" style="top:50px;width:210px;margin-left:-105px;background:var(--navy)"></div>

  <svg class="abs" style="left:0;top:0" width="669" height="269" viewBox="0 877 669 269">
    <circle cx="334" cy="1160" r="118" fill="none" stroke="#d4d4d4" stroke-width="18"/>
    <circle cx="334" cy="1160" r="108" fill="#fafafa"/>
    <g stroke="#9aa7b5" stroke-width="1">
      <line x1="286" y1="1006" x2="296" y2="1034"/>
      <line x1="366" y1="1006" x2="358" y2="1034"/>
      <line x1="228" y1="1036" x2="250" y2="1058"/>
      <line x1="424" y1="1036" x2="403" y2="1058"/>
      <line x1="193" y1="1098" x2="216" y2="1110"/>
      <line x1="460" y1="1098" x2="438" y2="1110"/>
    </g>
    <g fill="#4f7aa3">
      <circle cx="296" cy="1034" r="2.5"/><circle cx="358" cy="1034" r="2.5"/>
      <circle cx="250" cy="1058" r="2.5"/><circle cx="403" cy="1058" r="2.5"/>
      <circle cx="216" cy="1110" r="2.5"/><circle cx="438" cy="1110" r="2.5"/>
    </g>
    <g fill="#fff" stroke="#e2e2e2" stroke-width="2">
      <circle cx="286" cy="988" r="18"/><circle cx="366" cy="988" r="18"/>
      <circle cx="217" cy="1022" r="18"/><circle cx="436" cy="1022" r="18"/>
      <circle cx="175" cy="1093" r="18"/><circle cx="478" cy="1093" r="18"/>
    </g>
    <g fill="#111">
      <rect x="278" y="980" width="16" height="4"/><rect x="279" y="985" width="14" height="10" fill="none" stroke="#111" stroke-width="2"/><rect x="284" y="989" width="4" height="6"/>
      <rect x="357" y="982" width="18" height="13" rx="2"/><rect x="362" y="979" width="8" height="4" fill="none" stroke="#111" stroke-width="1.5"/><path d="M366 985v7M362.5 988.5h7" stroke="#fff" stroke-width="2"/>
      <path d="M208 1017 L217 1012 L226 1017Z"/><rect x="210" y="1018" width="14" height="10" fill="none" stroke="#111" stroke-width="2"/><rect x="208" y="1028" width="18" height="2"/><rect x="215" y="1021" width="4" height="4"/>
      <rect x="429" y="1015" width="6" height="15"/><rect x="436" y="1012" width="6" height="18"/><rect x="427" y="1030" width="18" height="1.5"/>
      <path d="M166 1086 L175 1081 L184 1086Z"/><rect x="167" y="1087" width="2.5" height="11"/><rect x="171.5" y="1087" width="2.5" height="11"/><rect x="176" y="1087" width="2.5" height="11"/><rect x="180.5" y="1087" width="2.5" height="11"/><rect x="165" y="1099" width="20" height="2"/>
      <path d="M469 1101 V1088 L474 1091 V1088 L479 1091 V1088 L484 1091 V1084 H487 V1101Z"/>
    </g>
  </svg>

  <span class="cov-label" style="left:242px;top:106px">SME</span>
  <span class="cov-label" style="left:394px;top:107px">Health care</span>
  <span class="cov-label" style="left:163px;top:140px">Banks</span>
  <span class="cov-label" style="left:467px;top:140px">Commercial</span>
  <span class="cov-label" style="left:86px;top:205px;width:64px;text-align:center;line-height:10px">Government entities</span>
  <span class="cov-label" style="left:503px;top:212px">Industrial</span>
  <span class="hub-name">Brisk Harbor</span>
</section>

<footer class="site-footer">
  <div class="foot-item" style="left:56px">
    <svg viewBox="0 0 11 12"><path d="M5.5 12 C2 7 1 5.5 1 4.5 A4.5 4.5 0 0 1 10 4.5 C10 5.5 9 7 5.5 12Z" fill="#ddd"/><circle cx="5.5" cy="4.5" r="1.6" fill="#1a1a1a"/></svg>
    Lorem ipsum dolor sit amet, adipiscing elit
  </div>
  <div class="foot-item" style="left:246px">
    <svg viewBox="0 0 11 12"><path d="M2 1 L4 1 L5 4 L3.5 5 Q5 8 7 9 L8 7.5 L11 8.5 L11 11 Q5 11.5 1 4Z" fill="#ddd"/></svg>
    123-456-7890
  </div>
  <div class="foot-item" style="left:334px">
    <svg viewBox="0 0 11 12"><rect x="0" y="2.5" width="11" height="7.5" fill="#ddd"/><path d="M0 2.5 L5.5 7 L11 2.5" fill="none" stroke="#1a1a1a" stroke-width="1"/></svg>
    info@briskharbor.com
  </div>
  <div class="social"><i></i><i></i><i></i><i></i></div>
</footer>
<div class="copyright">Copyright 2016 Briskharbor. All rights reserved.</div>

</body>
</html>
```